BOLD & MINIMALIST DESIGN NEEDED

We want a very bold but minimalistic business card design that is impactful and utilizes both sides of the business card. Our current logo is included for your use.

We want bold fonts and good use of negative space. We don't want the logo to overpower the design.

Target Market(s)

Professionals who are building new commercial buildings.

Industry/Entity Type

Construction

Contact Information for Business Card

Name, Title, email, office phone, cell phone, website

Font styles to use
Serif
Sans Serif

Requirements
Must have
• Bold design!

```html
<!DOCTYPE html>
<html lang="en">
<head>
<meta charset="utf-8">
<title>Summitline business card</title>
<link rel="stylesheet" href="https://fonts.googleapis.com/css2?family=Arimo:wght@400;700&display=swap">
<style>
  :root {
    --stage: #1c1c1c;
    --card-white: #f3f3f3;
    --brand-green: #7dbd3e;
    --ink: #222222;
    --ink-soft: #333333;
    --rule: #b9d49c;
    --white: #ffffff;
  }
  * { margin: 0; padding: 0; box-sizing: border-box; }
  html, body { width: 1200px; height: 1059px; overflow: hidden; }
  body {
    background: var(--stage);
    font-family: "Arimo", Arial, sans-serif;
    position: relative;
  }
  .card {
    position: absolute;
    width: 690px;
    height: 392px;
    border-radius: 16px;
    overflow: hidden;
  }
  .card-front { left: 256px; top: 89px; background: var(--card-white); }
  .card-back { left: 254px; top: 547px; background: var(--brand-green); }

  .wordmark {
    position: absolute;
    display: flex;
    align-items: center;
    gap: 10px;
    font-weight: 700;
    text-transform: uppercase;
    line-height: 1;
  }
  .wordmark-square { display: block; background: var(--brand-green); }
  .card-front .wordmark { left: 37px; top: 118px; font-size: 36px; color: var(--ink); letter-spacing: 0.5px; }
  .card-front .wordmark-square { width: 26px; height: 26px; }

  .person {
    position: absolute;
    right: 34px;
    top: 172px;
    text-align: right;
  }
  .person-name {
    font-weight: 700;
    font-size: 27px;
    color: var(--brand-green);
    line-height: 1;
  }
  .person-title {
    font-size: 18px;
    color: var(--ink-soft);
    margin-top: 3px;
    line-height: 1;
  }
  .accent-bar {
    position: absolute;
    right: 0;
    top: 177px;
    width: 21px;
    height: 41px;
    background: linear-gradient(to bottom, var(--brand-green), #b8dc8f);
  }
  .divider {
    position: absolute;
    left: 37px;
    top: 211px;
    width: 508px;
    height: 1px;
    background: var(--rule);
  }

  .contact-list {
    position: absolute;
    left: 37px;
    top: 252px;
    list-style: none;
  }
  .contact-item {
    display: flex;
    align-items: center;
    gap: 5px;
    height: 28px;
    font-size: 18px;
    color: var(--ink-soft);
  }
  .contact-icon { width: 13px; height: 13px; flex: none; }

  .card-back .wordmark {
    left: 50%;
    top: 50%;
    transform: translate(-50%, -50%);
    font-size: 56px;
    color: var(--white);
    gap: 16px;
  }
  .card-back .wordmark-square { width: 40px; height: 40px; background: var(--white); }
</style>
</head>
<body>
  <section class="card card-front" aria-label="Business card front">
    <div class="wordmark"><span class="wordmark-square"></span><span>Summitline</span></div>

    <div class="person">
      <p class="person-name">DANA WHITFIELD</p>
      <p class="person-title">Owner/CEO</p>
    </div>
    <span class="accent-bar"></span>
    <span class="divider"></span>

    <ul class="contact-list">
      <li class="contact-item">
        <svg class="contact-icon" viewBox="0 0 16 16" aria-hidden="true"><path fill="#7dbd3e" d="M3.5 1.5l2.5 0 1 3.5-1.8 1.2a8 8 0 0 0 4.6 4.6l1.2-1.8 3.5 1v2.5c0 1-1 1.5-2 1.5A12 12 0 0 1 2 4c0-1 .5-2.5 1.5-2.5z"/></svg>
        <span>07 5120 4480</span>
      </li>
      <li class="contact-item">
        <svg class="contact-icon" viewBox="0 0 16 16" aria-hidden="true"><rect x="4" y="1" width="8" height="14" rx="1.5" fill="none" stroke="#7dbd3e" stroke-width="1.6"/><rect x="7" y="12" width="2" height="1.2" fill="#7dbd3e"/></svg>
        <span>0422 615 907</span>
      </li>
      <li class="contact-item">
        <svg class="contact-icon" viewBox="0 0 16 16" aria-hidden="true"><rect x="1" y="3.5" width="14" height="9" fill="#7dbd3e"/><path d="M1 3.5l7 5 7-5" fill="none" stroke="#f3f3f3" stroke-width="1.2"/></svg>
        <span>hello@summitlinebuild.com</span>
      </li>
      <li class="contact-item">
        <svg class="contact-icon" viewBox="0 0 16 16" aria-hidden="true"><circle cx="8" cy="8" r="6.5" fill="none" stroke="#7dbd3e" stroke-width="1.6"/><path d="M1.5 8h13M8 1.5c-3 3.5-3 9.5 0 13M8 1.5c3 3.5 3 9.5 0 13" fill="none" stroke="#7dbd3e" stroke-width="1.2"/></svg>
        <span>www.summitlinebuild.com</span>
      </li>
    </ul>
  </section>

  <section class="card card-back" aria-label="Business card back">
    <div class="wordmark"><span class="wordmark-square"></span><span>Summitline</span></div>
  </section>
</body>
</html>
```